A Modern & Sleek "Coming Soon" Page for an A.I Recruiting App

For the “Coming Soon” website, a simple background with no people in it. I've attached an A.I image of what the page should generally look like.

- A single mobile phone as the main focus where the user actually clicks on the, “notify me” button (after entering their email address).
- In the background where the pillars/columns are seen in the example, should be subtle pad locks that are in their opened position with a key inside the lock. I've attached images to try to illustrate this idea, but they are far away in style from what I'm looking for.

SLOGAN: Unlocking the power of meaningful connections
LOGO/TITLE: Should be the name as shown in image with only the name "KelvoLink" on it
COLORS: Purplish/blue hues. Should not be too feminine
NOTE: The user should only click once when signing up/entering their email.

Product: A recruiting platform that matches employers/employees with A.I. and prioritizing cultural fit/values system before skills. The industry we are tackling first is the caregiving industry (nannies, tutors, elderly). All users will be background screened and that info lives on the blockchain. All users will have the option to review and be reviewed/rated.

```html
<!DOCTYPE html>
<html lang="en">
<head>
<meta charset="UTF-8">
<title>KelvoLink — Coming Soon</title>
<link rel="stylesheet" href="https://fonts.googleapis.com/css2?family=Josefin+Sans:wght@200;300&family=Arimo:wght@700&display=swap">
<style>
  :root {
    --bg-deep: #110770;
    --bg-mid: #1c0c8e;
    --glow-pink: #c2307f;
    --glow-violet: #5a1aa8;
    --phone-body: #0c0c10;
    --screen-top: #6a40b8;
    --screen-mid: #5330ac;
    --screen-low: #3d1f94;
    --accent: #b3317c;
    --accent-soft: #a23275;
    --brand-pink: #c33a8e;
    --text-light: #ffffff;
  }
  * { margin: 0; padding: 0; box-sizing: border-box; }
  html, body { width: 1200px; height: 640px; overflow: hidden; background: var(--bg-deep); }
  .page {
    position: relative;
    width: 1200px; height: 640px;
    overflow: hidden;
    background:
      radial-gradient(ellipse 170px 150px at 1180px 290px, rgba(194,48,127,.75), transparent 70%),
      radial-gradient(ellipse 150px 90px at 1010px 620px, rgba(194,48,127,.55), transparent 70%),
      radial-gradient(ellipse 260px 200px at 430px 120px, rgba(120,30,170,.35), transparent 70%),
      radial-gradient(ellipse 300px 200px at 100px 560px, rgba(5,2,40,.7), transparent 70%),
      linear-gradient(180deg, var(--bg-mid) 0%, var(--bg-deep) 100%);
    font-family: "Arimo", Arial, sans-serif;
  }
  .lock-visual {
    position: absolute;
    left: 496px; top: 376px;
    width: 600px; height: 224px;
    border-radius: 16px;
    background:
      radial-gradient(ellipse 160px 90px at 430px 130px, rgba(40,20,90,.9), transparent 70%),
      linear-gradient(160deg, rgba(130,80,220,.55) 0%, rgba(90,40,190,.55) 45%, rgba(40,15,120,.4) 100%);
    filter: blur(2px);
  }
  .phone {
    position: absolute;
    left: 172px; top: 40px;
    width: 232px; height: 568px;
    border-radius: 30px;
    background: var(--phone-body);
    padding: 10px;
    box-shadow: 0 20px 40px rgba(0,0,0,.45);
  }
  .phone-screen {
    position: relative;
    width: 100%; height: 100%;
    border-radius: 22px;
    overflow: hidden;
    background: linear-gradient(180deg, var(--screen-top), var(--screen-mid) 50%, var(--screen-low));
  }
  .phone-notch {
    position: absolute; left: 50%; top: -2px;
    width: 30px; height: 16px; margin-left: -15px;
    background: var(--phone-body);
    border-radius: 0 0 15px 15px;
  }
  .screen-waves { position: absolute; inset: 0; width: 100%; height: 100%; }
  .screen-logo {
    position: absolute; top: 86px; left: 0; right: 0;
    text-align: center;
    font-family: "Josefin Sans", sans-serif; font-weight: 200;
    font-size: 24px; letter-spacing: 1px; color: var(--text-light);
  }
  .screen-copy {
    position: absolute; top: 206px; left: 0; right: 0;
    text-align: center;
    font-size: 9.5px; line-height: 14px; color: var(--text-light);
  }
  .notify-button {
    position: absolute; left: 45px; top: 398px;
    width: 136px; height: 36px;
    border: none; border-radius: 18px;
    background: var(--accent-soft);
    color: var(--text-light);
    font-family: "Arimo", Arial, sans-serif; font-weight: 700; font-size: 10px;
    transform: rotate(-2deg);
  }
  .hero {
    position: absolute; left: 500px; top: 222px; width: 484px;
    text-align: center;
  }
  .brand-name {
    font-family: "Josefin Sans", sans-serif; font-weight: 200;
    font-size: 58px; letter-spacing: 3px; line-height: 60px;
    color: var(--brand-pink);
    text-transform: uppercase;
  }
  .slogan {
    margin-top: 16px;
    font-size: 20px; font-weight: 700; color: var(--text-light);
  }
  .signup-button {
    margin-top: 18px;
    width: 134px; height: 44px;
    border: none; border-radius: 22px;
    background: var(--accent);
    color: var(--text-light);
    font-family: "Arimo", Arial, sans-serif; font-weight: 700; font-size: 13px;
  }
</style>
</head>
<body>
<main class="page">
  <div class="lock-visual" role="img" aria-label="Open padlock with a key inserted, softly lit in purple"></div>

  <div class="phone">
    <div class="phone-screen">
      <svg class="screen-waves" viewBox="0 0 212 548" preserveAspectRatio="none" aria-hidden="true">
        <path d="M0 120 C60 70 130 110 212 150 L212 548 L0 548 Z" fill="#5834ad"/>
        <path d="M0 370 C70 330 140 300 212 290 L212 548 L0 548 Z" fill="#3f2196" opacity=".85"/>
      </svg>
      <div class="phone-notch"></div>
      <div class="screen-logo">KELVOLINK</div>
      <p class="screen-copy">Lorem ipsum dolor sit amet,<br>consectetur adipiscing elit, sed</p>
      <button class="notify-button">NOTIFY ME</button>
    </div>
  </div>

  <section class="hero">
    <h1 class="brand-name">KelvoLink</h1>
    <p class="slogan">Unlocking the power of meaningful connections</p>
    <button class="signup-button">SIGNUP</button>
  </section>
</main>
</body>
</html>
```